Brochure required

Looking at getting business brochure designed for my solar sales company. i will require a range of products to be listed on the brochure I require a simple/ elegent / professional looking brochure.

I am happy to provide designer with all the required information that must go into the brochure. otherwise please visit www.quillebartow.com.au and view the products which i would like to allocate into the brochure aswell as our company logo and a little about me section

```html
<!DOCTYPE html>
<html lang="en">
<head>
<meta charset="utf-8">
<title>Quillebartow – Energy solutions brochure</title>
<link href="https://fonts.googleapis.com/css2?family=Lato:wght@400;700;900&display=swap" rel="stylesheet">
<style>
  :root {
    --backdrop: #ebe5e1;
    --paper: #ffffff;
    --brand-blue: #1d84c6;
    --brand-green: #1fb68f;
    --brand-teal: #14a3a8;
    --gold: #c2a630;
    --ink: #3a3a3a;
    --ink-soft: #6b6b6b;
    --navy: #1d2a3a;
  }
  * { margin: 0; padding: 0; box-sizing: border-box; }
  html, body { width: 768px; height: 1200px; overflow: hidden; }
  body {
    background: var(--backdrop);
    font-family: "Lato", sans-serif;
    color: var(--ink);
    position: relative;
  }
  .page {
    position: absolute;
    width: 260px;
    height: 368px;
    background: var(--paper);
    overflow: hidden;
  }
  .single { left: 254px; top: 24px; box-shadow: 0 4px 14px rgba(0,0,0,.12); }
  .spread {
    position: absolute;
    left: 124px;
    width: 520px;
    height: 368px;
    box-shadow: 0 4px 14px rgba(0,0,0,.12);
  }
  .spread-outer { top: 416px; }
  .spread-inner { top: 808px; }
  .spread .page-left { left: 0; top: 0; }
  .spread .page-right { left: 260px; top: 0; }
  .gutter {
    position: absolute; left: 250px; top: 0; width: 20px; height: 368px;
    background: linear-gradient(90deg, rgba(0,0,0,0) 0%, rgba(0,0,0,.08) 50%, rgba(0,0,0,0) 100%);
    pointer-events: none;
  }
  .art { position: absolute; left: 0; top: 0; }

  .brand {
    position: absolute;
    display: flex; align-items: center; gap: 5px;
    font-weight: 900; color: var(--navy); letter-spacing: .2px;
  }
  .brand-mark { background: var(--brand-green); }

  /* cover */
  .cover .brand { left: 58px; top: 22px; font-size: 15px; }
  .cover .brand-mark { width: 12px; height: 12px; }
  .headline { position: absolute; left: 26px; top: 44px; line-height: 1.05; }
  .headline-lead { display: block; font-size: 19px; font-weight: 700; color: var(--brand-blue); }
  .headline-tail { display: block; font-size: 19px; font-weight: 700; color: var(--ink); padding-left: 48px; }

  /* back cover */
  .back .contact { position: absolute; left: 62px; top: 212px; width: 170px; }
  .back .brand { position: static; font-size: 12px; margin-bottom: 4px; }
  .back .brand-mark { width: 9px; height: 9px; }
  .call-label { font-size: 8px; font-weight: 700; color: var(--brand-blue); letter-spacing: .6px; }
  .phone { font-size: 16px; font-weight: 700; color: var(--ink); margin-bottom: 8px; }
  .contact-line { display: flex; flex-direction: column; align-items: center; width: 130px; font-size: 6.5px; color: var(--ink-soft); margin-bottom: 6px; gap: 2px; }

  /* inside */
  .copy { position: absolute; font-size: 5.4px; line-height: 1.45; color: var(--ink-soft); }
  .product-title { position: absolute; font-size: 8px; font-weight: 700; color: var(--brand-blue); letter-spacing: .3px; }
  .sub-title { position: absolute; font-size: 9px; font-weight: 700; color: var(--brand-blue); letter-spacing: .3px; }
</style>
</head>
<body>

<section class="page single cover" aria-label="Front cover">
  <svg class="art" width="260" height="368" viewBox="0 0 260 368">
    <defs>
      <linearGradient id="fieldA" x1="0" y1="0" x2="0" y2="1">
        <stop offset="0" stop-color="#7fa9cf"/>
        <stop offset=".38" stop-color="#f2c88a"/>
        <stop offset=".55" stop-color="#45586e"/>
        <stop offset="1" stop-color="#5d8a2e"/>
      </linearGradient>
    </defs>
    <path d="M96 368 C98 290 108 222 128 204 L260 200 L260 368 Z" fill="var(--brand-green)"/>
    <circle cx="172" cy="292" r="88" fill="url(#fieldA)" stroke="#fff" stroke-width="4" role="img" aria-label="Photo of solar panels in a grassy field at sunrise"/>
  </svg>
  <div class="brand"><span class="brand-mark"></span>Quillebartow</div>
  <h1 class="headline">
    <span class="headline-lead">Energy solutions for a</span>
    <span class="headline-tail">changing world</span>
  </h1>
</section>

<section class="spread spread-outer" aria-label="Outer spread">
  <div class="page page-left back">
    <svg class="art" width="260" height="368" viewBox="0 0 260 368">
      <defs>
        <linearGradient id="installer" x1="0" y1="0" x2="1" y2="1">
          <stop offset="0" stop-color="#6f9ccc"/>
          <stop offset=".5" stop-color="#b9cde0"/>
          <stop offset="1" stop-color="#2f3f5c"/>
        </linearGradient>
        <linearGradient id="wave" x1="0" y1="0" x2="1" y2="0">
          <stop offset="0" stop-color="var(--brand-teal)"/>
          <stop offset="1" stop-color="var(--brand-blue)"/>
        </linearGradient>
      </defs>
      <circle cx="62" cy="95" r="108" fill="none" stroke="var(--gold)" stroke-width="5"/>
      <circle cx="54" cy="92" r="100" fill="url(#installer)" role="img" aria-label="Photo of an installer in a helmet fitting a solar panel on a roof"/>
      <path d="M0 330 C90 352 190 326 260 262 L260 368 L0 368 Z" fill="url(#wave)"/>
    </svg>
    <div class="contact">
      <div class="brand"><span class="brand-mark"></span>Quillebartow</div>
      <div class="call-label">CALL US NOW</div>
      <div class="phone">0400 555 172</div>
      <div class="contact-line">
        <svg width="9" height="9" viewBox="0 0 10 10"><circle cx="5" cy="5" r="5" fill="var(--brand-blue)"/><rect x="2.5" y="3.3" width="5" height="3.4" fill="none" stroke="#fff" stroke-width=".8"/><path d="M2.5 3.3 L5 5.3 L7.5 3.3" fill="none" stroke="#fff" stroke-width=".8"/></svg>
        <span>info@quillebartow.com.au</span>
      </div>
      <div class="contact-line">
        <svg width="9" height="9" viewBox="0 0 10 10"><circle cx="5" cy="5" r="5" fill="var(--brand-blue)"/><circle cx="5" cy="5" r="2.6" fill="none" stroke="#fff" stroke-width=".8"/><path d="M2.4 5 H7.6" stroke="#fff" stroke-width=".7"/></svg>
        <span>www.quillebartow.com.au</span>
      </div>
    </div>
  </div>

  <div class="page page-right cover">
    <svg class="art" width="260" height="368" viewBox="0 0 260 368">
      <defs>
        <linearGradient id="fieldB" x1="0" y1="0" x2="0" y2="1">
          <stop offset="0" stop-color="#7fa9cf"/>
          <stop offset=".38" stop-color="#f2c88a"/>
          <stop offset=".55" stop-color="#45586e"/>
          <stop offset="1" stop-color="#5d8a2e"/>
        </linearGradient>
      </defs>
      <path d="M96 368 C98 290 108 222 128 204 L260 200 L260 368 Z" fill="var(--brand-green)"/>
      <circle cx="172" cy="292" r="88" fill="url(#fieldB)" stroke="#fff" stroke-width="4" role="img" aria-label="Photo of solar panels in a grassy field at sunrise"/>
    </svg>
    <div class="brand"><span class="brand-mark"></span>Quillebartow</div>
    <h2 class="headline">
      <span class="headline-lead">Energy solutions for a</span>
      <span class="headline-tail">changing world</span>
    </h2>
  </div>
  <div class="gutter"></div>
</section>

<section class="spread spread-inner" aria-label="Inner spread">
  <div class="page page-left">
    <svg class="art" width="260" height="368" viewBox="0 0 260 368">
      <defs>
        <linearGradient id="panelA" x1="0" y1="0" x2="1" y2="1">
          <stop offset="0" stop-color="#3c4b66"/><stop offset="1" stop-color="#1e2a40"/>
        </linearGradient>
        <linearGradient id="panelB" x1="0" y1="0" x2="1" y2="1">
          <stop offset="0" stop-color="#2e4d8a"/><stop offset="1" stop-color="#1b2e5a"/>
        </linearGradient>
        <linearGradient id="farm" x1="0" y1="0" x2="0" y2="1">
          <stop offset="0" stop-color="#c9d9e6"/><stop offset=".45" stop-color="#52637a"/><stop offset="1" stop-color="#4d7a2c"/>
        </linearGradient>
      </defs>
      <rect x="18" y="56" width="62" height="60" fill="url(#panelA)" role="img" aria-label="Product photo of a monocrystalline solar panel"/>
      <rect x="18" y="152" width="62" height="56" fill="url(#panelB)" role="img" aria-label="Product photo of two blue solar panels"/>
      <path d="M0 276 C90 254 180 272 260 336 L260 368 L0 368 Z" fill="url(#farm)" role="img" aria-label="Photo of a large solar farm under a clear sky"/>
      <path d="M0 268 C90 246 184 264 260 328" fill="none" stroke="var(--brand-green)" stroke-width="4"/>
    </svg>
    <p class="copy" style="left:18px;top:14px;width:226px;">Quillebartow works with trusted solar makers to bring you quality panels. Every product we list is tested, certified and backed by strong warranties for homes and business.</p>
    <h3 class="product-title" style="left:92px;top:58px;">TORVAN 270W</h3>
    <p class="copy" style="left:92px;top:72px;width:150px;">A proven high output module with strong resistance to heat, salt mist and harsh weather conditions.</p>
    <p class="copy" style="left:18px;top:122px;width:226px;">This panel sets a new standard of reliability and performance for rooftop solar.</p>
    <h3 class="product-title" style="left:92px;top:154px;">KESTRA OSPREY PERC 60M 300W</h3>
    <p class="copy" style="left:92px;top:168px;width:150px;">A highly efficient monocrystalline panel from a Tier 1 maker at an affordable price.</p>
    <p class="copy" style="left:18px;top:216px;width:226px;">Its five busbar cell design lifts efficiency while improving its look.</p>
  </div>

  <div class="page page-right">
    <svg class="art" width="260" height="368" viewBox="0 0 260 368">
      <defs>
        <linearGradient id="invRed" x1="0" y1="0" x2="0" y2="1">
          <stop offset="0" stop-color="#e9e9e9"/><stop offset=".6" stop-color="#d8d8d8"/><stop offset=".61" stop-color="#d6312b"/><stop offset="1" stop-color="#b3241f"/>
        </linearGradient>
        <linearGradient id="invGrey" x1="0" y1="0" x2="0" y2="1">
          <stop offset="0" stop-color="#e9e9e9"/><stop offset=".6" stop-color="#d4d4d4"/><stop offset=".61" stop-color="#4a4a4a"/><stop offset="1" stop-color="#2e2e2e"/>
        </linearGradient>
      </defs>
      <rect x="188" y="42" width="54" height="58" rx="5" fill="url(#invRed)" role="img" aria-label="Product photo of a hybrid inverter with red base"/>
      <rect x="188" y="124" width="54" height="58" rx="5" fill="url(#invGrey)" role="img" aria-label="Product photo of a single phase inverter with grey base"/>
      <g class="ppa-chart">
        <line x1="40" y1="270" x2="40" y2="346" stroke="#9a9a9a" stroke-width=".6"/>
        <line x1="40" y1="346" x2="232" y2="346" stroke="#9a9a9a" stroke-width=".6"/>
        <rect x="44" y="300" width="30" height="46" fill="var(--brand-blue)" opacity=".85"/>
        <rect x="44" y="296" width="188" height="5" fill="var(--brand-green)" opacity=".7"/>
        <g stroke="#c8c8c8" stroke-width=".5">
          <line x1="80" y1="301" x2="80" y2="346"/><line x1="88" y1="302" x2="88" y2="346"/><line x1="96" y1="303" x2="96" y2="346"/>
          <line x1="104" y1="304" x2="104" y2="346"/><line x1="112" y1="306" x2="112" y2="346"/><line x1="120" y1="308" x2="120" y2="346"/>
          <line x1="128" y1="310" x2="128" y2="346"/><line x1="136" y1="312" x2="136" y2="346"/><line x1="144" y1="314" x2="144" y2="346"/>
          <line x1="152" y1="317" x2="152" y2="346"/><line x1="160" y1="320" x2="160" y2="346"/><line x1="168" y1="323" x2="168" y2="346"/>
          <line x1="176" y1="326" x2="176" y2="346"/><line x1="184" y1="329" x2="184" y2="346"/><line x1="192" y1="332" x2="192" y2="346"/>
          <line x1="200" y1="335" x2="200" y2="346"/><line x1="208" y1="338" x2="208" y2="346"/><line x1="216" y1="341" x2="216" y2="346"/>
        </g>
        <path d="M74 300 C130 304 180 322 232 344" fill="none" stroke="#3a3a3a" stroke-width=".8" stroke-dasharray="2 1.5"/>
        <line x1="76" y1="274" x2="76" y2="300" stroke="#9a9a9a" stroke-width=".5"/>
      </g>
    </svg>
    <h3 class="sub-title" style="left:20px;top:18px;">QUORVALT HYBRID</h3>
    <p class="copy" style="left:20px;top:31px;width:160px;">One of the first high voltage hybrid inverters on the market.</p>
    <p class="copy" style="left:20px;top:46px;width:160px;">The Vela Hybrid lets homes store solar energy in batteries and use it at night, with smart monitoring built in.</p>
    <h3 class="sub-title" style="left:20px;top:100px;">QUORVALT AXIS 6.0 INVERTER</h3>
    <p class="copy" style="left:20px;top:113px;width:160px;">A great choice for larger residential or small commercial systems on a single phase.</p>
    <p class="copy" style="left:20px;top:130px;width:160px;">The Axis offers high efficiency, Wi-Fi connectivity and an extended warranty, in sizes from 3kW to 8kW.</p>
    <h3 class="sub-title" style="left:20px;top:194px;">PPA'S</h3>
    <p class="copy" style="left:20px;top:207px;width:222px;">A Power Purchase Agreement (PPA) gets you on the path to energy independence with no upfront costs.</p>
    <p class="copy" style="left:20px;top:223px;width:222px;">A PPA is a fixed term plan through which you pay for electricity generated by an installed system for a fixed c/kWh rate.</p>
    <p class="copy" style="left:20px;top:239px;width:222px;">Typically, the fixed c/kWh rate is lower than your current energy retailer charge and protects your business from rate rises during the term.</p>
  </div>
  <div class="gutter"></div>
</section>

</body>
</html>
```